Catalogue Design Project

We need a catalog design for a new private university called Redwell Institute Bayshore (see website www.rwi-bs.org). The catalog should be about 30 pages maximum and will include items such as General Information, Academic schedule, department descriptions, program descriptions, course descriptions, school policies, student services, admissions, San diego Lifestyle, etc.
I will provide the text but I need a professional design with regard to page layouts. I have provided some examples.
Ok, i posted the catalog content, just missing course descriptions.
Target Market(s)
Young Professionals, Foreign Students
Industry/Entity Type
University
Look and feel
Each slider illustrates characteristics of the customer's brand and the style your logo design should communicate.

```html
<!DOCTYPE html>
<html lang="en">
<head>
<meta charset="utf-8">
<title>TESOL Certificate — Certificate Programs</title>
<link href="https://fonts.googleapis.com/css2?family=Carlito:wght@400;700&display=swap" rel="stylesheet">
<style>
  :root {
    --ink: #1a1a1a;
    --brand-blue: #2f5f8f;
    --rule-blue: #6d8fb0;
    --dot-grey: #a3a3a3;
    --paper: #ffffff;
    --footer-grey: #8a8a8a;
    --book-light: #f3ead8;
    --book-warm: #d9c39a;
  }
  * { margin: 0; padding: 0; box-sizing: border-box; }
  html, body { width: 927px; height: 1200px; overflow: hidden; background: var(--paper); }
  .page {
    position: relative;
    width: 927px;
    height: 1200px;
    font-family: "Carlito", "Calibri", sans-serif;
    color: var(--ink);
    background: var(--paper);
    overflow: hidden;
  }
  .header-mark {
    position: absolute;
    left: 60px;
    top: 40px;
    width: 152px;
    height: 38px;
    background: linear-gradient(90deg, #4d7aa6 0%, #b2b2b2 30%, #b2b2b2 75%, #4d7aa6 100%);
    border-radius: 10px;
    opacity: 0.85;
  }
  .header-visual {
    position: absolute;
    right: 0;
    top: 0;
    width: 370px;
    height: 100px;
    background: linear-gradient(90deg, rgba(243,234,216,0) 0%, var(--book-light) 35%, var(--book-warm) 100%);
  }
  .header-rule {
    position: absolute;
    left: 0;
    top: 102px;
    width: 927px;
    height: 2px;
    background: var(--rule-blue);
  }
  .section-banner {
    position: absolute;
    right: 0;
    top: 102px;
    width: 405px;
    height: 38px;
  }
  .section-banner svg { position: absolute; inset: 0; }
  .section-banner span {
    position: absolute;
    right: 16px;
    top: 4px;
    color: #fff;
    font-size: 30px;
    letter-spacing: 0.5px;
    line-height: 32px;
  }
  .content {
    position: absolute;
    left: 82px;
    top: 193px;
    width: 806px;
    font-size: 19px;
    line-height: 32.2px;
  }
  .content h1 {
    text-align: center;
    font-size: 24px;
    font-weight: 700;
    line-height: 32px;
    margin-bottom: 1px;
  }
  .content p.body-copy { text-align: justify; }
  .content strong { font-weight: 700; }
  .content .label { text-decoration: underline; }
  .content .spacer { height: 32.2px; }
  .footer-rule {
    position: absolute;
    left: 0;
    top: 1158px;
    width: 927px;
    height: 1px;
    background: var(--rule-blue);
  }
  .footer-mark {
    position: absolute;
    right: 40px;
    top: 1170px;
    font-size: 13px;
    color: var(--footer-grey);
    letter-spacing: 0.3px;
  }
</style>
</head>
<body>
<div class="page">
  <div class="header-mark" role="img" aria-label="Decorative dot pattern in blue and grey"></div>
  <div class="header-visual" role="img" aria-label="Photograph of an open book"></div>
  <div class="header-rule"></div>
  <div class="section-banner">
    <svg width="405" height="38" viewBox="0 0 405 38" aria-hidden="true">
      <polygon points="0,0 405,0 405,38 26,38" fill="var(--brand-blue)"/>
    </svg>
    <span>CERTIFICATE PROGRAMS</span>
  </div>

  <main class="content">
    <h1>TESOL Certificate</h1>
    <p class="body-copy">The Certificate in Teaching-English-to-Speakers-of-Other-Languages (TESOL) offers coursework which allows participants to acquire the specialized training and skills needed for a successful career teaching English as a second language, either in the U.S. or in another country. Emphasis is placed on essential ESL skills ranging from teaching pronunciation, listening, speaking, writing, and classroom management to specialized teaching skills such as teaching Business English and children, as well as tutoring private students.</p>
    <p class="body-copy">The fundamentals of English grammar and how to teach it through stimulating and engaging lessons are also emphasized. In addition to in-classroom training, students will also participate in teaching actual foreign students currently studying English. Students of the TESOL certificate program will receive weekly progress reports in addition to ample experience to ensure readiness at time of graduation.</p>
    <p class="body-copy">Completion and attainment of TESOL Credential improves successful job offers, and thus finally, the course will offer job information for teachers looking to obtain positions overseas. Our internationally experienced teachers focus on ensuring your passport to success.</p>
    <p><strong>Hours:</strong> 15 hours per week</p>
    <p><strong>Length:</strong> 5 weeks per course</p>
    <div class="spacer"></div>
    <p class="label">Course:</p>
    <p>ENG 600 TESOL</p>
    <p class="label">Learning Outcome:</p>
    <p class="body-copy">Gain the needed instruction and experience to become a teacher of English either in the United States or abroad.</p>
  </main>

  <div class="footer-rule"></div>
  <div class="footer-mark">8::: REDWELL INSTITUTE</div>
</div>
</body>
</html>
```